Verdo Consultants Exhibition Booth Design. Cannabis Legal Consultancy

We require a design for the following artwork in PDF of Jpeg high resolution format with these specifications, a 5cm bleed outside and a 10cm safe inside bleed. A tension fabric backdrop 200cm wide and 231cm high. (example loaded) Please see our website www.theverdoconsultants.co.uk
Attached are company logos and head shots for inclusion. You will see our colour schemes from the website. It should announce who we are and provide the company website.

```html
<!DOCTYPE html>
<html lang="en">
<head>
<meta charset="utf-8">
<title>The Verdo Consultants – Exhibition Backdrop</title>
<link rel="stylesheet" href="https://fonts.googleapis.com/css2?family=Bebas+Neue&family=Montserrat:wght@500;600&family=Open+Sans:wght@600&display=swap">
<style>
  :root {
    --brand-blue: #1450f0;
    --charcoal: #474a48;
    --ink: #2b2d2e;
    --panel: #fbfbfb;
    --stage: #e4e7e7;
    --white: #ffffff;
  }
  * { margin: 0; padding: 0; box-sizing: border-box; }
  html, body { width: 1200px; height: 977px; overflow: hidden; }
  body { background: var(--stage); position: relative; }

  .backdrop {
    position: absolute; left: 210px; top: 38px;
    width: 780px; height: 900px;
    background: var(--panel);
    overflow: hidden;
    box-shadow: 0 6px 24px rgba(0,0,0,.08);
  }
  .backdrop-art { position: absolute; inset: 0; }

  .brand {
    position: absolute; left: 512px; top: 66px;
    font-family: "Montserrat", sans-serif; font-weight: 600;
    color: var(--brand-blue); line-height: 1;
  }
  .brand-the { font-size: 22px; display: block; }
  .brand-name { font-size: 34px; display: block; margin-top: 4px; }
  .brand-sub { font-size: 29px; display: block; margin-top: 2px; }
  .brand-url {
    position: absolute; right: 22px; top: 182px; text-align: right;
    font-family: "Open Sans", sans-serif; font-weight: 600; font-size: 14px; color: var(--ink);
  }

  .services {
    position: absolute; right: 20px; top: 222px; text-align: right;
    font-family: "Bebas Neue", sans-serif; font-weight: 400; color: var(--brand-blue);
    font-size: 68px; line-height: .92;
  }

  .tagline {
    position: absolute; right: 20px; top: 522px; text-align: right;
    font-family: "Montserrat", sans-serif; font-weight: 500; color: var(--white);
    font-size: 40px; line-height: 1.18;
  }

  .name-tag {
    position: absolute; height: 44px; border-radius: 22px;
    background: var(--brand-blue); color: var(--white);
    font-family: "Bebas Neue", sans-serif; font-size: 30px;
    display: flex; align-items: center; justify-content: center; padding-top: 3px;
  }
  .name-tag--owen { left: 322px; top: 702px; width: 180px; }
  .name-tag--daniel { left: 62px; top: 800px; width: 205px; }

  .site-url {
    position: absolute; right: 20px; top: 806px;
    font-family: "Open Sans", sans-serif; font-weight: 600; font-size: 30px; color: var(--ink);
  }
</style>
</head>
<body>
<main class="backdrop">
  <svg class="backdrop-art" width="780" height="900" viewBox="0 0 780 900">
    <defs>
      <radialGradient id="compass-tone" cx="55%" cy="45%" r="65%">
        <stop offset="0" stop-color="#8ea3a6"/>
        <stop offset=".55" stop-color="#4d5a5e"/>
        <stop offset="1" stop-color="#20292c"/>
      </radialGradient>
      <linearGradient id="portrait-light" x1="0" y1="0" x2="0" y2="1">
        <stop offset="0" stop-color="#d9dcdd"/>
        <stop offset="1" stop-color="#1e2c44"/>
      </linearGradient>
      <linearGradient id="portrait-dark" x1="0" y1="0" x2="0" y2="1">
        <stop offset="0" stop-color="#3a3d3f"/>
        <stop offset="1" stop-color="#1b1d22"/>
      </linearGradient>
    </defs>

    <!-- compass feature circle -->
    <circle cx="50" cy="320" r="318" fill="none" stroke="var(--charcoal)" stroke-width="5" stroke-dasharray="1120 900" transform="rotate(-80 50 320)"/>
    <circle cx="50" cy="320" r="288" fill="none" stroke="var(--brand-blue)" stroke-width="9" stroke-dasharray="420 2000" transform="rotate(-95 50 320)"/>
    <circle cx="50" cy="320" r="238" fill="none" stroke="var(--charcoal)" stroke-width="20"/>
    <g role="img" aria-label="Close-up photo of a compass with its needle pointing to the word Answers">
      <circle cx="50" cy="320" r="226" fill="url(#compass-tone)"/>
    </g>

    <!-- tagline band -->
    <rect x="520" y="508" width="260" height="190" fill="var(--charcoal)"/>

    <!-- portrait: Owen Marsh -->
    <circle cx="410" cy="562" r="126" fill="var(--panel)"/>
    <circle cx="410" cy="562" r="122" fill="none" stroke="var(--charcoal)" stroke-width="5" stroke-dasharray="420 400" transform="rotate(-60 410 562)"/>
    <circle cx="410" cy="562" r="104" fill="none" stroke="var(--brand-blue)" stroke-width="4" stroke-dasharray="330 400" transform="rotate(100 410 562)"/>
    <circle cx="410" cy="562" r="88" fill="none" stroke="var(--charcoal)" stroke-width="6"/>
    <g role="img" aria-label="Head-and-shoulders portrait of consultant Owen Marsh">
      <circle cx="410" cy="562" r="84" fill="url(#portrait-light)"/>
    </g>

    <!-- portrait: Daniel Hart -->
    <circle cx="165" cy="650" r="140" fill="var(--panel)"/>
    <circle cx="165" cy="650" r="137" fill="none" stroke="var(--charcoal)" stroke-width="5" stroke-dasharray="500 400" transform="rotate(-20 165 650)"/>
    <circle cx="165" cy="650" r="118" fill="none" stroke="var(--brand-blue)" stroke-width="4" stroke-dasharray="380 400" transform="rotate(90 165 650)"/>
    <circle cx="165" cy="650" r="100" fill="none" stroke="var(--charcoal)" stroke-width="6"/>
    <g role="img" aria-label="Head-and-shoulders portrait of consultant Daniel Hart">
      <circle cx="165" cy="650" r="96" fill="url(#portrait-dark)"/>
    </g>

    <!-- brand mark circle -->
    <circle cx="445" cy="116" r="52" fill="none" stroke="var(--brand-blue)" stroke-width="5"/>

    <!-- url underline -->
    <line x1="348" y1="860" x2="760" y2="856" stroke="var(--brand-blue)" stroke-width="2"/>
    <circle cx="348" cy="860" r="7" fill="var(--brand-blue)"/>
  </svg>

  <div class="brand">
    <span class="brand-the">THE</span>
    <span class="brand-name">VERDO</span>
    <span class="brand-sub">CONSULTANTS</span>
  </div>
  <p class="brand-url">www.theverdoconsultants.co.uk</p>

  <h1 class="services">Assessment<br>Advice<br>Implementation</h1>

  <p class="tagline">Be Careful<br>Who You<br>Listen To</p>

  <p class="name-tag name-tag--owen">Owen Marsh</p>
  <p class="name-tag name-tag--daniel">Daniel Hart</p>

  <p class="site-url">www.theverdoconsultants.co.uk</p>
</main>
</body>
</html>
```